Velvet Riot Rising Line of Sparkling Wine & Spirits

Back info: Nora Beth Quill Owner 555-318-4402 1480 E. Harlow Ave, Bldg. 2, & 3, Ambervale Ro. 95871
Sparkling Wines & Memorabilia www.velvetriotrising.com
Ok I have uploaded the winning design. The color that I am after is the Fushia, Raspberry, Red, Matte Satin Matalic Finish. With a 24 Karet Gold color Foil. The Bottle is on the top row and it's the 2nd Bottle in. That is the Color that I want. This is the style of font. Make sure that you put what we're advertising. Good Luck to you all. Warmest regards, Nora
21 & up UniSex
Sparkling Wine and Memorabilia
there listed up above.....

```html
<!DOCTYPE html>
<html lang="en">
<head>
<meta charset="utf-8">
<title>Velvet Riot Rising – Business Card</title>
<link rel="stylesheet" href="https://fonts.googleapis.com/css2?family=Arimo:wght@400;700&display=swap">
<style>
  :root {
    --backdrop: #e3e3e3;
    --paper: #ffffff;
    --fuchsia: #d4187f;
    --fuchsia-bright: #e01a99;
    --raspberry: #9c1558;
    --gold: #e8a33c;
    --ink: #555555;
    --logo-ink: #3a3a3a;
  }
  * { box-sizing: border-box; margin: 0; padding: 0; }
  html, body { width: 1200px; height: 1200px; overflow: hidden; }
  body {
    background: var(--backdrop);
    font-family: "Arimo", Arial, sans-serif;
    position: relative;
  }
  .card {
    position: absolute;
    left: 264px;
    width: 688px;
    height: 394px;
    overflow: hidden;
  }
  .card--front { top: 159px; background: var(--paper); }
  .card--back {
    top: 653px;
    background: radial-gradient(ellipse 60% 70% at 50% 45%, var(--fuchsia-bright) 0%, #c21a83 45%, var(--raspberry) 100%);
  }
  .bottle {
    position: absolute;
    border-radius: 10px 10px 8px 8px;
    background: linear-gradient(90deg, #a8145f 0%, #e4229b 45%, #b3186a 100%);
  }
  .card--front .bottle { left: 171px; top: 99px; width: 54px; height: 176px; }
  .card--back .bottle { left: 102px; top: 65px; width: 74px; height: 256px; }
  .divider {
    position: absolute; left: 256px; top: 111px;
    width: 1px; height: 154px; background: #cfcfcf;
  }
  .contact { position: absolute; left: 288px; top: 118px; }
  .contact__name {
    font-weight: 700; font-size: 26px; color: var(--fuchsia);
    line-height: 30px; letter-spacing: 0.3px;
  }
  .contact__role { font-size: 17px; color: var(--gold); line-height: 18px; }
  .contact__address {
    margin-top: 22px; font-size: 16px; color: var(--ink); line-height: 21px;
  }
  .contact__phone {
    margin-top: 13px; font-size: 16px; color: var(--ink);
    display: flex; align-items: center; gap: 10px;
  }
  .contact__phone svg { width: 14px; height: 14px; }
  .footer-band { position: absolute; left: 0; top: 362px; width: 688px; height: 32px; }
  .footer-band__url {
    position: absolute; left: 455px; top: 368px;
    font-size: 16px; color: #ffffff;
  }
  .brand { position: absolute; left: 193px; top: 160px; width: 363px; }
  .brand__name {
    font-weight: 700; font-size: 37px; color: var(--logo-ink);
    line-height: 60px; white-space: nowrap;
  }
  .brand__rule { height: 1px; background: rgba(255,255,255,0.35); margin-top: 6px; }
  .brand__tagline {
    margin-top: 10px; font-size: 17px; color: #ffffff;
    letter-spacing: 1.6px; white-space: nowrap;
  }
  .brand__tagline strong { font-weight: 700; }
</style>
</head>
<body>
  <section class="card card--front">
    <div class="bottle" role="img" aria-label="Fuchsia sparkling wine bottle with gold foil neck"></div>
    <div class="divider"></div>
    <div class="contact">
      <p class="contact__name">NORA BETH QUILL</p>
      <p class="contact__role">Owner</p>
      <p class="contact__address">E. Harlow Ave<br>Bldg. 2, &amp; 3, Ambervale Ro. 95871</p>
      <p class="contact__phone">
        <svg viewBox="0 0 24 24" aria-hidden="true"><path fill="#d4187f" d="M6.6 10.8a15.5 15.5 0 0 0 6.6 6.6l2.2-2.2c.3-.3.7-.4 1-.2 1.1.4 2.3.6 3.6.6.6 0 1 .4 1 1V20c0 .6-.4 1-1 1A17 17 0 0 1 3 4c0-.6.4-1 1-1h3.5c.6 0 1 .4 1 1 0 1.3.2 2.5.6 3.6.1.3 0 .7-.2 1z"/></svg>
        555-318-4402 1480
      </p>
    </div>
    <svg class="footer-band" viewBox="0 0 688 32" aria-hidden="true">
      <defs>
        <linearGradient id="bronze" x1="0" x2="1" y1="0" y2="0">
          <stop offset="0" stop-color="#6b3d14"/>
          <stop offset="0.5" stop-color="#b77a36"/>
          <stop offset="1" stop-color="#6b3d14"/>
        </linearGradient>
      </defs>
      <polygon points="0,0 398,0 390,14 0,14" fill="url(#bronze)"/>
      <rect x="0" y="18" width="688" height="14" fill="#c2197a"/>
      <polygon points="404,0 688,0 688,32 388,32 396,18 400,6" fill="#c2197a"/>
    </svg>
    <p class="footer-band__url">www.velvetriotrising.com</p>
  </section>

  <section class="card card--back">
    <div class="bottle" role="img" aria-label="Fuchsia sparkling wine bottle with gold foil neck"></div>
    <div class="brand">
      <p class="brand__name">Velvet Riot Rising</p>
      <div class="brand__rule"></div>
      <p class="brand__tagline">SPARKLING <strong>WINES &amp; MEMORABILIA</strong></p>
    </div>
  </section>
</body>
</html>
```